The Brandwell Firm

We need a new design for our letterhead and envelopes. We are a personal injury and criminal defense firm so we need something modern and clean, but more on the professional/traditional side. Our new logo has two colors and is attached to the file so we need something that works well with those colors/matches the design. The following information needs to be on the letterhead:
Phone: (555) 214-3370
Fax: (555) 214-5186
Toll-Free: (888) 431-2059
Post Office Box 4721
Millbrook, SC 29555-4721
HarmClaimCounsel.example
PalmettoTrialAdvocates.example

Target Market(s)

Clients, government agencies, other law firms

Industry/Entity Type

Legal

Font styles to use
Sans Serif
Other font styles liked:
• Arial

Colors

Designer to choose colors to be used in the design.

Requirements
Must have
• Must look professional and clean, modern
Nice to have
• I would like to see a design that works with the logo but does not distract from the content that will be printed on it
Should not have
• Too many colors or crazy designs.

```html
<!DOCTYPE html>
<html lang="en">
<head>
<meta charset="utf-8">
<title>The Brandwell Firm — Stationery</title>
<link href="https://fonts.googleapis.com/css2?family=Poppins:wght@300;400&family=Roboto:wght@400;500&family=Cinzel:wght@600&display=swap" rel="stylesheet">
<style>
  :root {
    --backdrop: #dedede;
    --paper: #eeeeee;
    --paper-shade: #e2e2e2;
    --brand-red: #d31f26;
    --brand-blue: #2e3192;
    --stripe: #f2f2f2;
    --ink: #4a4a4a;
    --ink-soft: #5b5b5b;
    --rule: #c9c9c9;
  }
  * { margin: 0; padding: 0; box-sizing: border-box; }
  html, body { width: 1200px; height: 877px; overflow: hidden; background: var(--backdrop); }
  .stage { position: relative; width: 1200px; height: 877px; }

  .sheet {
    position: absolute;
    background: linear-gradient(90deg, #f3f3f3 0%, var(--paper) 45%, var(--paper-shade) 100%);
    box-shadow: 0 2px 8px rgba(0,0,0,.12);
    overflow: hidden;
  }

  .wordmark {
    font-family: 'Cinzel', serif;
    font-weight: 600;
    color: var(--brand-blue);
    letter-spacing: .5px;
    white-space: nowrap;
  }

  /* Letterhead */
  .letterhead { left: 69px; top: 64px; width: 527px; height: 742px; }
  .letterhead .wordmark { position: absolute; left: 34px; top: 72px; font-size: 17px; }
  .contact {
    position: absolute; left: 390px; top: 44px;
    padding-left: 7px; border-left: 1px solid var(--rule);
    font-family: 'Roboto', sans-serif; font-style: normal; font-size: 7.4px; line-height: 10px; color: var(--ink-soft);
  }
  .contact .address { margin-bottom: 6px; }
  .contact-line { display: flex; align-items: center; gap: 4px; }
  .contact-line svg { width: 7px; height: 7px; fill: var(--brand-blue); }
  .salutation {
    position: absolute; left: 46px; top: 206px;
    font-family: 'Poppins', sans-serif; font-weight: 300; font-size: 13.5px; color: var(--ink);
  }
  .letter-body {
    position: absolute; left: 46px; top: 247px; width: 440px;
    font-family: 'Poppins', sans-serif; font-weight: 300; font-size: 7.3px; line-height: 11.4px; color: var(--ink);
    text-align: justify;
  }
  .letter-body p { margin-bottom: 11.4px; }
  .closing { margin-top: 22px; }
  .signature {
    position: absolute; left: 44px; top: 517px; width: 96px; height: 32px;
    background: linear-gradient(90deg, rgba(46,49,146,.18), rgba(46,49,146,.06));
    border-radius: 4px;
  }

  .footer-band { position: absolute; left: 0; bottom: 0; width: 100%; height: 64px; }
  .footer-band svg { position: absolute; inset: 0; width: 100%; height: 100%; }
  .footer-links {
    position: absolute; bottom: 6px; left: 0; right: 0; text-align: center;
    font-family: 'Roboto', sans-serif; font-size: 7.6px; line-height: 9px; color: #fff;
  }

  /* Envelopes */
  .envelope-red { left: 645px; top: 190px; width: 531px; height: 240px; }
  .envelope-blue { left: 611px; top: 281px; width: 531px; height: 241px; }
  .flap { position: absolute; left: 0; top: 0; width: 100%; height: 75px; }
  .flap svg { width: 100%; height: 100%; display: block; }
  .flap-name {
    position: absolute; left: 0; right: 0; top: 30px; text-align: center;
    font-family: 'Cinzel', serif; font-weight: 600; font-size: 9px; color: #fff; letter-spacing: .5px;
  }

  .envelope-front { left: 614px; top: 562px; width: 532px; height: 242px; }
  .envelope-front .wordmark { position: absolute; left: 24px; top: 50px; font-size: 14px; }
  .return-address {
    position: absolute; left: 32px; top: 90px;
    font-family: 'Roboto', sans-serif; font-size: 7.4px; line-height: 10px; color: var(--ink-soft);
  }
</style>
</head>
<body>
<main class="stage">

  <section class="sheet letterhead">
    <div class="wordmark">The Brandwell Firm</div>
    <address class="contact">
      <div class="address">Post Office Box 4721<br>Millbrook, SC 29555-4721</div>
      <div class="contact-line"><svg viewBox="0 0 10 10"><path d="M2 0.5 L3.8 2.6 L2.9 3.7 Q4 6 6.3 7.1 L7.4 6.2 L9.5 8 L8.3 9.5 Q2.5 8.6 0.5 1.7 Z"/></svg>(555) 214-3370</div>
      <div class="contact-line"><svg viewBox="0 0 10 10"><path d="M0.5 2 H9.5 V8.5 H0.5 Z M0.5 2 L5 5.5 L9.5 2" stroke="#eee" stroke-width=".8"/></svg>(555) 214-5186</div>
      <div class="contact-line"><svg viewBox="0 0 10 10"><circle cx="5" cy="5" r="4.5"/><path d="M1 5 H9 M5 0.5 V9.5" stroke="#eee" stroke-width=".7"/></svg>(888) 431-2059</div>
    </address>

    <div class="salutation">Dear Mr. Harlow,</div>
    <div class="letter-body">
      <p>Lorem ipsum dolor sit amet, consectetur adipiscing elit. Donec orci purus, luctus vitae dignissim eu, iaculis sed purus. Vivamus faucibus, ipsum nec aliquet viverra, leo mauris condimentum ligula, sit amet sagittis enim ligula quis arcu. Nam egestas tortor id nisi porttitor mattis. In tortor ante, ultricies in suscipit a, tempus non massa. Vivamus et auctor mi. Fusce vel massa nulla. Phasellus nec eros mauris, et scelerisque orci.</p>
      <p>Donec malesuada orci vitae nulla accumsan porta a id massa. Quisque accumsan iaculis magna sit amet fringilla. Maecenas consequat, magna eget tincidunt semper, odio nibh rutrum mi, id feugiat ante nisi eu risus. Vestibulum nunc orci, rhoncus a placerat in, ultricies in mi. Cras mattis varius eros, vel fringilla nisi suscipit eget. Quisque scelerisque sagittis nulla at porttitor.</p>
      <p>Sed id augue vitae urna euismod commodo aliquet a quam. Pellentesque arcu velit, cursus et malesuada ut, consequat et diam. Nullam erat sem, rhoncus id ullamcorper vitae, rhoncus et arcu. In ultricies ultricies nulla, ut rutrum nisi iaculis at. Donec eu magna a metus ornare faucibus. Fusce aliquet faucibus ultricies. Morbi semper, est id tincidunt gravida, sem arcu adipiscing lacus, ac bibendum nulla leo eu purus. Quisque nec diam sed risus consectetur a ccumsan quis quis nibh. Vestibulum id purus lorem.</p>
      <p>It is a long established fact that a reader will be distracted by the readable content of a page when looking at its layout. The point of using Lorem Ipsum is that it has a more-or-less normal distribution of letters, as opposed to using 'Content here, content here', making it look like readable English. Many desktop publishing packages</p>
      <p class="closing">Sincerely,</p>
    </div>
    <div class="signature" role="img" aria-label="Handwritten signature of Evan Harlow"></div>

    <div class="footer-band">
      <svg viewBox="0 0 527 64" preserveAspectRatio="none">
        <path d="M48 64 Q300 -36 527 30 V64 Z" fill="var(--brand-red)"/>
        <path d="M60 64 Q300 -24 527 38 V64 Z" fill="var(--stripe)"/>
        <path d="M70 64 Q300 -16 527 48 V64 Z" fill="var(--brand-blue)"/>
      </svg>
      <div class="footer-links">www.HarmClaimCounsel.example | www.PalmettoTrialAdvocates.example</div>
    </div>
  </section>

  <section class="sheet envelope-red">
    <div class="flap">
      <svg viewBox="0 0 531 75" preserveAspectRatio="none"><path d="M0 0 H531 L522 50 Q518 74 494 74 H37 Q13 74 9 50 Z" fill="var(--brand-red)"/></svg>
      <div class="flap-name">The Brandwell Firm</div>
    </div>
  </section>

  <section class="sheet envelope-blue">
    <div class="flap">
      <svg viewBox="0 0 531 75" preserveAspectRatio="none"><path d="M0 0 H531 L522 50 Q518 74 494 74 H37 Q13 74 9 50 Z" fill="var(--brand-blue)"/></svg>
      <div class="flap-name">The Brandwell Firm</div>
    </div>
  </section>

  <section class="sheet envelope-front">
    <div class="wordmark">The Brandwell Firm</div>
    <div class="return-address">Post Office Box 4721<br>Millbrook, SC 29555-4721</div>
    <div class="footer-band">
      <svg viewBox="0 0 532 64" preserveAspectRatio="none">
        <path d="M48 64 Q300 -36 532 30 V64 Z" fill="var(--brand-red)"/>
        <path d="M60 64 Q300 -24 532 38 V64 Z" fill="var(--stripe)"/>
        <path d="M70 64 Q300 -16 532 48 V64 Z" fill="var(--brand-blue)"/>
      </svg>
      <div class="footer-links">www.HarmClaimCounsel.example | www.PalmettoTrialAdvocates.example</div>
    </div>
  </section>

</main>
</body>
</html>
```